Create a memorable Stationary for Security Software Company

Velbrantix is the worldwide leader in securing the Internet. Making Internet communications and critical data secure, reliable and available everywhere has been and continues to be our ongoing vision. We are committed to staying focused on real customer needs and to developing new and innovative security solutions that redefine the security landscape.

Industry/Entity Type

Internet

Font styles to use
Serif
Sans Serif
Script

Colors
0792cd
33a6d7
85cae6

```html
<!DOCTYPE html>
<html lang="en">
<head>
<meta charset="utf-8">
<title>Velbrantix Business Card</title>
<link href="https://fonts.googleapis.com/css2?family=Open+Sans:wght@400;600;700&display=swap" rel="stylesheet">
<style>
  :root {
    --blue-deep: #0792cd;
    --blue-mid: #33a6d7;
    --blue-light: #85cae6;
    --ink: #3a3a3a;
    --white: #ffffff;
    --backdrop: #e9ecef;
  }
  * { margin: 0; padding: 0; box-sizing: border-box; }
  html, body {
    width: 1200px; height: 1120px; overflow: hidden;
    background: var(--backdrop);
    font-family: "Open Sans", sans-serif;
  }
  .canvas { position: relative; width: 1200px; height: 1120px; }
  .card {
    position: absolute; left: 180px; width: 840px; height: 480px;
    overflow: hidden;
    box-shadow: 0 10px 30px rgba(0,0,0,0.18);
  }
  .card--front { top: 60px; background: var(--blue-light); }
  .card--back { top: 580px; background: var(--white); }

  .brand {
    position: absolute; display: flex; align-items: center; gap: 16px;
    color: var(--blue-deep); font-weight: 700;
  }
  .brand__dot {
    border-radius: 50%; background: var(--blue-deep); flex: none;
  }
  .card--front .brand { left: 50%; top: 160px; transform: translateX(-50%); font-size: 58px; }
  .card--front .brand__dot { width: 52px; height: 52px; }
  .card--back .brand { left: 60px; top: 205px; font-size: 46px; }
  .card--back .brand__dot { width: 42px; height: 42px; }

  .front__url {
    position: absolute; left: 0; right: 0; top: 330px; text-align: center;
    font-size: 26px; letter-spacing: 4px; color: var(--ink);
  }

  .back__panel { position: absolute; inset: 0; }
  .back__details {
    position: absolute; right: 48px; top: 62px; text-align: right;
    color: var(--white);
  }
  .person__name { font-size: 27px; font-weight: 700; line-height: 1.2; }
  .person__title { font-size: 22px; line-height: 1.2; }
  .contact { margin-top: 42px; list-style: none; font-size: 20px; line-height: 1.6; }
  .contact li { display: flex; justify-content: flex-end; align-items: center; gap: 10px; }
  .contact svg { width: 18px; height: 18px; flex: none; }
  .address { margin-top: 14px; font-size: 20px; line-height: 1.4; }
</style>
</head>
<body>
<main class="canvas">
  <section class="card card--front" aria-label="Card front">
    <div class="brand"><span class="brand__dot"></span><span>Velbrantix</span></div>
    <p class="front__url">www.velbrantix.com</p>
  </section>

  <section class="card card--back" aria-label="Card back">
    <svg class="back__panel" viewBox="0 0 840 480" width="840" height="480" aria-hidden="true">
      <path d="M440 0 C565 120 565 360 430 480 L840 480 L840 0 Z" fill="var(--blue-mid)"/>
      <path d="M456 0 C582 120 582 360 446 480" fill="none" stroke="var(--white)" stroke-width="4"/>
      <path d="M466 0 C594 120 594 360 456 480 L840 480 L840 0 Z" fill="var(--blue-deep)"/>
    </svg>

    <div class="brand"><span class="brand__dot"></span><span>Velbrantix</span></div>

    <div class="back__details">
      <p class="person__name">Your Name</p>
      <p class="person__title">Title</p>
      <ul class="contact">
        <li>
          <svg viewBox="0 0 20 20" aria-hidden="true"><path d="M5 2 L8 2 L9 6 L7 8 C8 11 9 12 12 13 L14 11 L18 12 L18 15 C18 17 16 18 14 18 C8 17 3 12 2 6 C2 4 3 2 5 2 Z" fill="var(--white)"/></svg>
          <span>012-345-6789</span>
        </li>
        <li>
          <svg viewBox="0 0 20 20" aria-hidden="true"><rect x="5" y="1" width="10" height="18" rx="2" fill="var(--white)"/><rect x="7" y="4" width="6" height="9" fill="var(--blue-deep)"/></svg>
          <span>012-345-6789</span>
        </li>
        <li>
          <svg viewBox="0 0 20 20" aria-hidden="true"><rect x="1" y="4" width="18" height="12" rx="1" fill="var(--white)"/><path d="M1 5 L10 11 L19 5" fill="none" stroke="var(--blue-deep)" stroke-width="1.6"/></svg>
          <span>info@velbrantix.com</span>
        </li>
        <li>
          <svg viewBox="0 0 20 20" aria-hidden="true"><circle cx="10" cy="10" r="8" fill="none" stroke="var(--white)" stroke-width="1.8"/><ellipse cx="10" cy="10" rx="3.5" ry="8" fill="none" stroke="var(--white)" stroke-width="1.5"/><path d="M2 10 H18 M3.5 6 H16.5 M3.5 14 H16.5" stroke="var(--white)" stroke-width="1.3"/></svg>
          <span>www.velbrantix.com</span>
        </li>
      </ul>
      <p class="address">Street Name, City Name<br>Zipcode-012345</p>
    </div>
  </section>
</main>
</body>
</html>
```